Holistic Psychologist needs contemporary business card

I am a psychologist working with adult clients face to face and online. The card needs to work for clients and also referring doctors and medical professionals. It needs to look warm, safe and trustable for clients, but clean and professional enough for doctors. Sometimes I also work in a corporate context.

I am holistic in my approach (mind-body-spirit) so anything conveying connection or integration or wholeness would be good. But again, clean and contemporary please. It can have a little bit of personality.

Probably warm tones and plenty white space to write on one side.

My web pages:
http://mwtherapy.com.au
https://www.facebook.com/HelenaMorrowTherapy?ref=hl
Updates

Hi Designers .. I have decided I do need a new logo before finalising a design for the business cards.  I hope to have this available in 4 days from now.

Kindly,

Helena

New logo now posted, same brief.  Balance of masculine and feminine elements, plenty of white space on one side please.

Keen to see some card designs, thank-you.

Target Market(s)

Audience 1 - Males and females aged 25 years + seeking counselling or coaching. Audience 2 - doctors and health professionals who refer clients.

Industry/Entity Type

Medical

Contact Information for Business Card

Logo

Helena Morrow
Registered Psychologist

M: 0481 552 903
www.mwtherapy.com.au
helena@mwtherapy.com.au
Little blue Facebook icon, with "helena morrow therapy" printed near it.

Font styles to use
Sans Serif

Requirements
Nice to have
• You might want to play with the words "wholly you"
Should not have
• Nothing cutesy or too literal

```html
<!DOCTYPE html>
<html lang="en">
<head>
<meta charset="utf-8">
<title>helena morrow therapy – business card</title>
<link rel="stylesheet" href="https://fonts.googleapis.com/css2?family=Questrial&family=Cormorant+Garamond:ital,wght@1,500&display=swap">
<style>
  :root {
    --stage: #e4e2e0;
    --purple-light: #9c22a8;
    --purple-dark: #6b0f79;
    --white: #ffffff;
    --paper-shade: #eeeeee;
    --ink: #111111;
    --ink-soft: #333333;
    --accent-red: #d8262c;
    --social-blue: #3b5998;
    --lilac-text: #e6c9ea;
  }
  * { box-sizing: border-box; margin: 0; padding: 0; }
  html, body { width: 1200px; height: 871px; overflow: hidden; }
  body {
    background: var(--stage);
    position: relative;
    font-family: "Questrial", "Century Gothic", sans-serif;
  }
  .card {
    position: absolute;
    width: 600px;
    height: 343px;
    box-shadow: 0 8px 24px rgba(0,0,0,0.25);
  }
  /* Front */
  .card-front {
    left: 70px; top: 70px;
    background: radial-gradient(circle at 40% 35%, var(--purple-light), var(--purple-dark) 90%);
    color: var(--white);
  }
  .front-wordmark {
    position: absolute; left: 90px; top: 96px;
    font-size: 46px; line-height: 1.05; letter-spacing: 0.5px;
    color: var(--white);
  }
  .front-tagline {
    position: absolute; left: 320px; top: 208px;
    font-family: "Cormorant Garamond", Georgia, serif;
    font-style: italic; font-weight: 500;
    font-size: 24px; color: var(--accent-red);
  }
  .front-social {
    position: absolute; left: 240px; top: 290px;
    display: flex; align-items: center; gap: 10px;
    font-size: 16px; color: var(--lilac-text); letter-spacing: 0.5px;
  }
  .social-square {
    width: 16px; height: 16px; background: var(--social-blue);
  }
  /* Back */
  .card-back {
    left: 530px; top: 460px;
    background: linear-gradient(120deg, var(--white) 55%, var(--paper-shade));
    color: var(--ink);
  }
  .back-wordmark {
    position: absolute; left: 40px; top: 40px;
    display: flex; align-items: center; gap: 14px;
  }
  .wordmark-dot {
    width: 18px; height: 18px; border-radius: 50%;
    background: var(--accent-red);
  }
  .wordmark-name {
    font-size: 40px; line-height: 1; color: var(--ink);
  }
  .contact-list {
    position: absolute; left: 40px; top: 200px;
    list-style: none;
    display: flex; flex-direction: column; gap: 12px;
    font-size: 16px; color: var(--ink-soft);
  }
  .contact-item { display: flex; align-items: center; gap: 14px; }
  .contact-icon { width: 14px; height: 14px; fill: var(--accent-red); }
</style>
</head>
<body>

<section class="card card-front">
  <div class="front-wordmark">helena morrow<br>therapy</div>
  <div class="front-tagline">wholly you</div>
  <div class="front-social">
    <span class="social-square" aria-hidden="true"></span>
    <span>helena morrow therapy</span>
  </div>
</section>

<section class="card card-back">
  <div class="back-wordmark">
    <span class="wordmark-dot" aria-hidden="true"></span>
    <span class="wordmark-name">helena morrow therapy</span>
  </div>
  <ul class="contact-list">
    <li class="contact-item">
      <svg class="contact-icon" viewBox="0 0 16 16" aria-hidden="true"><path d="M3 2l3 0 1 4-2 1c1 2 2 3 4 4l1-2 4 1 0 3c-1 1-2 1-3 1C6 14 2 10 2 5c0-1 0-2 1-3z"/></svg>
      <span>0481 552 903</span>
    </li>
    <li class="contact-item">
      <svg class="contact-icon" viewBox="0 0 16 16" aria-hidden="true"><path d="M1 3h14v10H1z M2 4l6 5 6-5" fill="none" stroke="#d8262c" stroke-width="1.6"/></svg>
      <span>helena@mwtherapy.com.au</span>
    </li>
    <li class="contact-item">
      <svg class="contact-icon" viewBox="0 0 16 16" aria-hidden="true"><g fill="none" stroke="#d8262c" stroke-width="1.4"><circle cx="8" cy="8" r="6.5"/><ellipse cx="8" cy="8" rx="3" ry="6.5"/><path d="M1.5 8h13M2.5 5h11M2.5 11h11"/></g></svg>
      <span>www.mwtherapy.com.au</span>
    </li>
  </ul>
</section>

</body>
</html>
```